Brindle Sky Port needs a new upscale business card design for our high end aircraft hangar complex

Brindle Sky Port (BSP) is a large, upscale jet hangar complex in the US housing expensive aircraft. We need a new business card design, using our current logo. We will be attending a industry convention and need a card design that will stand out and be remembered by aircraft owners and private pilots.

Target Market(s)

Aircraft pilots or owners looking for a new upscale hangar

Industry/Entity Type

Airport

Contact Information for Business Card

I like to use very heavy card stock, 400#, double sided. Square, no rounded edges please.

Colors
3276b5
0255a3
85abd2

Requirements
Must have
• An expensive, classy design, vivid colors.
Nice to have
• Needs to look very expensive and classy, and have some "pop". Designer must be able to download or copy my current typeface or fonts.
• One card side might be black with the "Logo and Brindle Sky Port Double line image in blue (or try gold, or glossy black), and perhaps have a grayed out "K720 jet silhouette". The other card side would have our contact info, and perhaps the "BSP Logo only". I'd like my contact info 'stacked', not in a paragraph format.
Should not have
• Should not look "too busy". Having a double-sided card will help.

```html
<!DOCTYPE html>
<html lang="en">
<head>
<meta charset="UTF-8">
<title>Brindle Sky Port – Business Card</title>
<link href="https://fonts.googleapis.com/css2?family=Open+Sans:wght@400;600;700&display=swap" rel="stylesheet">
<style>
  :root {
    --stage: #8f8f8f;
    --card: #0b0b0c;
    --card-edge: #1a1a1c;
    --brand-blue: #3276b5;
    --brand-light: #85abd2;
    --text: #e6e6e6;
    --rule: #6b6b6b;
    --jet-shade: #1c1d20;
  }
  * { margin: 0; padding: 0; box-sizing: border-box; }
  html, body { width: 1200px; height: 844px; overflow: hidden; }
  body {
    background: var(--stage);
    font-family: "Open Sans", Arial, sans-serif;
    position: relative;
  }
  .card {
    position: absolute;
    top: 273px;
    width: 520px;
    height: 297px;
    background: var(--card);
    border: 1px solid var(--card-edge);
    box-shadow: 0 14px 30px rgba(0,0,0,.35);
    overflow: hidden;
  }
  .card--contact { left: 50px; }
  .card--brand { left: 630px; }

  .jet-silhouette {
    position: absolute;
    background: radial-gradient(ellipse at center, var(--jet-shade) 0%, rgba(28,29,32,0.4) 55%, rgba(11,11,12,0) 75%);
  }
  .card--brand .jet-silhouette { left: 20px; top: 10px; width: 300px; height: 270px; }
  .card--contact .jet-silhouette { left: 230px; top: 70px; width: 260px; height: 220px; }

  .wordmark {
    position: absolute;
    color: var(--brand-blue);
    font-weight: 700;
    text-transform: uppercase;
    line-height: 1;
  }
  .card--brand .wordmark { right: 44px; top: 98px; text-align: left; }
  .card--brand .wordmark__initials { font-size: 64px; letter-spacing: 6px; display: block; }
  .card--brand .wordmark__name { font-size: 19px; letter-spacing: 2px; display: block; margin-top: 6px; }
  .card--contact .wordmark { left: 30px; top: 32px; font-size: 54px; letter-spacing: 5px; }

  .rule {
    position: absolute;
    height: 1px;
    background: var(--rule);
  }
  .rule--top { left: 44px; right: 20px; top: 116px; }
  .rule--bottom { left: 300px; right: 20px; top: 203px; }

  .phone-list {
    position: absolute;
    left: 30px;
    top: 126px;
    list-style: none;
    color: var(--text);
    font-size: 13px;
    line-height: 18px;
  }
  .phone-list li { display: flex; align-items: center; gap: 8px; }
  .phone-list svg { width: 11px; height: 11px; fill: var(--brand-light); }

  .person {
    position: absolute;
    right: 26px;
    top: 160px;
    text-align: right;
  }
  .person__name { color: var(--brand-blue); font-weight: 700; font-size: 16px; letter-spacing: 1px; text-transform: uppercase; }
  .person__title { color: var(--text); font-size: 13px; }

  .address {
    position: absolute;
    right: 26px;
    top: 212px;
    text-align: right;
    color: var(--text);
    font-size: 14px;
    line-height: 19px;
    font-style: normal;
  }
</style>
</head>
<body>
  <section class="card card--contact" aria-label="Contact side">
    <div class="jet-silhouette" role="img" aria-label="Faint K720 jet silhouette"></div>
    <div class="wordmark">BSP</div>
    <div class="rule rule--top"></div>
    <ul class="phone-list">
      <li><svg viewBox="0 0 12 12"><path d="M2.5 1 L4.5 1 L5 3.5 L3.8 4.5 Q5 7 7.5 8.2 L8.5 7 L11 7.5 L11 9.5 Q10 11 8.5 11 Q2 10 1 3.5 Q1 2 2.5 1 Z"/></svg>555 214 7730</li>
      <li><svg viewBox="0 0 12 12"><path d="M3 0.5 H9 V11.5 H3 Z M4 1.8 V9 H8 V1.8 Z"/></svg>555 309 6182</li>
      <li><svg viewBox="0 0 12 12"><path d="M3 1 H9 V4 H11 V10 H1 V4 H3 Z M4 2 V4 H8 V2 Z"/></svg>555 471 0256</li>
      <li><svg viewBox="0 0 12 12"><path d="M0.5 2.5 H11.5 V9.5 H0.5 Z M1.5 3.5 L6 6.8 L10.5 3.5 Z"/></svg>evan@brindlesky.com</li>
    </ul>
    <div class="person">
      <div class="person__name">Evan Harlow</div>
      <div class="person__title">CEO / Founder</div>
    </div>
    <div class="rule rule--bottom"></div>
    <address class="address">
      4120 Larkspur Way<br>
      Juneau, Alaska 99801<br>
      www.brindlesky.com
    </address>
  </section>

  <section class="card card--brand" aria-label="Brand side">
    <div class="jet-silhouette" role="img" aria-label="Faint K720 jet silhouette"></div>
    <div class="wordmark">
      <span class="wordmark__initials">BSP</span>
      <span class="wordmark__name">Brindle Sky Port</span>
    </div>
  </section>
</body>
</html>
```